Travel Agency Website - Simple General

Need a 7 page simple design that is pretty repetitive. Need to be able to load quickly that is SEO optimized. Trying to give ideas on what they can do, be personal as we are local, but at the same time come across as professional and get information easily with little burden.

- Landing Page
- Brimwell Vacations Page
- Family Trips
- Road Trips from Texas
- Other Destinations
- About Us Page
- Contact Us Page

Target Market(s)

Families

Coding

Coded - Design and coding required

Number of Pages Required

5+ page

Colors

Designer to choose colors to be used in the design.

Requirements
Must have
• Like it to flow easily with our logo. Use that for colors, etc.

```html
<!DOCTYPE html>
<html lang="en">
<head>
<meta charset="utf-8">
<title>Meander &amp; Hum Travel Co.</title>
<link href="https://fonts.googleapis.com/css2?family=Amaranth:wght@400;700&family=Signika:wght@400;600&display=swap" rel="stylesheet">
<style>
:root{
  --navy:#04182a;
  --ink:#3b4a5a;
  --gold:#d4a04a;
  --teal:#2f7f86;
  --teal-soft:#6fb0ae;
  --white:#ffffff;
  --sky-top:#1a6fd0;
  --sky-mid:#3d8fd8;
  --rock:#b45a3a;
  --rock-dark:#7a3a2c;
}
*{margin:0;padding:0;box-sizing:border-box}
html,body{width:1200px;height:825px;overflow:hidden;background:var(--white)}
body{position:relative;font-family:"Signika",sans-serif}
.sidebar{position:absolute;left:0;top:0;width:245px;height:630px;background:var(--white)}
.brand{position:absolute;left:78px;top:17px;width:96px;height:80px;display:flex;align-items:center;justify-content:center;text-align:center;font-family:"Amaranth",sans-serif;font-weight:700;font-size:19px;line-height:1.05;color:var(--teal)}
.nav{position:absolute;left:85px;top:152px;list-style:none}
.nav li{width:129px;height:48px;border-bottom:1px dashed var(--gold);font-weight:600;font-size:14px;letter-spacing:.2px;color:var(--ink);text-transform:uppercase;display:flex;align-items:center;white-space:nowrap}
.nav li:last-child{border-bottom:none}
.nav li.active{color:#1f2d3c}
.nav li.active svg{margin-left:5px}
.hero{position:absolute;left:245px;top:0;width:955px;height:630px;
  background:linear-gradient(180deg,var(--sky-top) 0%,var(--sky-mid) 28%,#7ea6b4 40%,var(--rock) 58%,#c47a52 75%,var(--rock-dark) 100%)}
.contact{position:absolute;top:15px;display:flex;align-items:center;gap:8px;color:var(--white);font-family:"Amaranth",sans-serif;font-weight:700;font-size:19px;white-space:nowrap}
.contact.email{left:265px}
.contact.phone{left:667px}
.tile{position:absolute;width:210px;height:210px;border-radius:50%;border:4px solid var(--white);
  display:flex;flex-direction:column;align-items:center;justify-content:center;text-align:center;
  color:var(--white);font-family:"Amaranth",sans-serif;font-weight:700;font-size:24px;line-height:1.15}
.tile svg{margin-bottom:2px}
.tile.brimwell{left:87px;top:208px;background:radial-gradient(circle at 50% 40%,#5e7f9a,#2c4c6c)}
.tile.family{left:260px;top:214px;background:radial-gradient(circle at 50% 45%,#7c8f94,#3e5a66)}
.tile.road{left:434px;top:208px;background:radial-gradient(circle at 50% 45%,#8a8c88,#4a5e66)}
.tile.other{left:629px;top:210px;background:radial-gradient(circle at 50% 40%,#7d97a6,#4c6a7a)}
.footer{position:absolute;left:0;top:630px;width:1200px;height:195px;background:var(--navy);color:var(--white)}
.footer-brand{position:absolute;left:118px;top:52px;width:120px;height:108px;display:flex;align-items:center;justify-content:center;text-align:center;font-family:"Amaranth",sans-serif;font-weight:700;font-size:24px;line-height:1.05;color:var(--teal-soft)}
.social{position:absolute;top:82px;display:flex;align-items:center;gap:9px;font-family:"Amaranth",sans-serif;font-size:17px}
.social .dot{width:22px;height:22px;border-radius:50%;background:var(--gold)}
.social.one{left:783px}
.social.two{left:991px}
.copyright{position:absolute;right:106px;top:126px;font-size:15px;letter-spacing:-.2px}
.copyright span{color:var(--teal-soft)}
</style>
</head>
<body>
<aside class="sidebar">
  <div class="brand">Meander &amp; Hum</div>
  <ul class="nav">
    <li class="active">Home<svg width="14" height="16" viewBox="0 0 14 16"><path d="M7 0 L8.3 6.7 L14 8 L8.3 9.3 L7 16 L5.7 9.3 L0 8 L5.7 6.7Z" fill="#d4a04a"/></svg></li>
    <li>Brimwell Vacations</li>
    <li>Family Trips</li>
    <li>Texas Road Trips</li>
    <li>Other Destinations</li>
    <li>About Us</li>
    <li>Contact Us</li>
  </ul>
</aside>

<main class="hero" role="img" aria-label="Photo of riders on horseback on a trail through red rock canyon hoodoos under a blue sky">
  <div class="contact email">
    <svg width="38" height="38" viewBox="0 0 38 38"><rect x="6" y="6" width="26" height="26" transform="rotate(45 19 19)" fill="#d4a04a"/><rect x="12" y="14" width="14" height="10" rx="1" fill="#fff"/><path d="M12 15 L19 20 L26 15" stroke="#d4a04a" stroke-width="1.4" fill="none"/></svg>
    hello@meanderandhum.com
  </div>
  <div class="contact phone">
    <svg width="38" height="38" viewBox="0 0 38 38"><rect x="6" y="6" width="26" height="26" transform="rotate(45 19 19)" fill="#d4a04a"/><path d="M14 12 L17 12 L18 16 L16 17.5 C17 20 18.5 21.5 21 22.5 L22.5 20.5 L26 21.5 L26 24.5 C19 25 13 19 14 12Z" fill="#fff"/></svg>
    555.014.2288
  </div>

  <div class="tile brimwell" role="img" aria-label="Photo of a fairytale castle"><svg width="20" height="22" viewBox="0 0 14 16"><path d="M7 0 L8.3 6.7 L14 8 L8.3 9.3 L7 16 L5.7 9.3 L0 8 L5.7 6.7Z" fill="#d4a04a"/></svg>Brimwell<br>Vacations</div>
  <div class="tile family" role="img" aria-label="Photo of a family taking a selfie by a bridge"><svg width="20" height="22" viewBox="0 0 14 16"><path d="M7 0 L8.3 6.7 L14 8 L8.3 9.3 L7 16 L5.7 9.3 L0 8 L5.7 6.7Z" fill="#d4a04a"/></svg>Family<br>Trips</div>
  <div class="tile road" role="img" aria-label="Photo of friends around a small red car"><svg width="20" height="22" viewBox="0 0 14 16"><path d="M7 0 L8.3 6.7 L14 8 L8.3 9.3 L7 16 L5.7 9.3 L0 8 L5.7 6.7Z" fill="#d4a04a"/></svg>Texas Road<br>Trips</div>
  <div class="tile other" role="img" aria-label="Photo of an airport runway with a plane"><svg width="20" height="22" viewBox="0 0 14 16"><path d="M7 0 L8.3 6.7 L14 8 L8.3 9.3 L7 16 L5.7 9.3 L0 8 L5.7 6.7Z" fill="#d4a04a"/></svg>Other<br>Destinations</div>
</main>

<footer class="footer">
  <div class="footer-brand">Meander &amp; Hum</div>
  <div class="social one"><span class="dot"></span>Facelink</div>
  <div class="social two"><span class="dot"></span>Picstream</div>
  <p class="copyright">© 2026 <span>MEANDER &amp; HUM</span>. All right reserved.</p>
</footer>
</body>
</html>
```